Business Card Design

I already have a company logo for my company. I have a logo for the manufacturer we represent. I want a professional business card design.

```html
<!DOCTYPE html>
<html lang="en">
<head>
<meta charset="utf-8">
<title>Beacon Guard Co – Business Card</title>
<link rel="stylesheet" href="https://fonts.googleapis.com/css2?family=Montserrat:wght@400;500;700;800&display=swap">
<style>
  :root {
    --stage: #2f2f2f;
    --gold-top: #8b6f12;
    --gold-bottom: #6a5a22;
    --brand-red: #e2262c;
    --ink: #2a2a2a;
    --ink-soft: #444444;
    --paper: #ffffff;
    --silver: #dcdcdc;
    --accent-gold: #c9a227;
  }
  * { box-sizing: border-box; margin: 0; padding: 0; }
  html, body {
    width: 1200px; height: 688px; overflow: hidden;
    background: var(--stage);
    font-family: "Montserrat", sans-serif;
  }
  .canvas {
    position: relative; width: 1200px; height: 688px;
    display: flex; align-items: center; justify-content: center; gap: 40px;
  }
  .card {
    position: relative; width: 540px; height: 308px; overflow: hidden;
  }
  /* Front */
  .card--front {
    background: linear-gradient(160deg, var(--gold-top) 0%, var(--gold-bottom) 100%);
    display: flex; align-items: center; justify-content: center;
  }
  .brand {
    display: flex; align-items: center; gap: 12px;
  }
  .brand__mark {
    width: 22px; height: 22px; background: var(--brand-red);
  }
  .brand__name {
    font-weight: 800; letter-spacing: 0.04em; text-transform: uppercase; line-height: 1;
  }
  .card--front .brand__name { color: var(--silver); font-size: 34px; }
  .card--front .brand__rule {
    position: absolute; left: 150px; right: 150px; top: 186px;
    height: 4px; background: var(--accent-gold);
  }
  /* Back */
  .card--back { background: var(--paper); }
  .card--back .brand {
    position: absolute; left: 30px; top: 60px;
  }
  .card--back .brand__name { color: var(--brand-red); font-size: 22px; }
  .card--back .brand__mark { width: 14px; height: 14px; }
  .card--back .brand__rule {
    position: absolute; left: 30px; top: 94px; width: 250px; height: 3px;
    background: var(--accent-gold);
  }
  .emblem-area {
    position: absolute; right: 0; top: 0; width: 230px; height: 230px;
  }
  .contact {
    position: absolute; left: 30px; top: 130px; color: var(--ink);
  }
  .contact__name { color: var(--brand-red); font-weight: 700; font-size: 20px; }
  .contact__title { font-size: 11px; font-weight: 500; color: var(--ink-soft); margin-top: 2px; }
  .contact__address { font-size: 11px; margin-top: 14px; line-height: 1.35; }
  .contact__list { list-style: none; margin-top: 14px; font-size: 11px; line-height: 1.7; }
  .contact__list li { display: flex; align-items: center; gap: 8px; }
  .contact__list svg { width: 10px; height: 10px; fill: var(--brand-red); flex: none; }
</style>
</head>
<body>
<main class="canvas">
  <section class="card card--front" aria-label="Card front">
    <div class="brand">
      <span class="brand__mark"></span>
      <span class="brand__name">Beacon Guard Co</span>
    </div>
    <span class="brand__rule"></span>
  </section>

  <section class="card card--back" aria-label="Card back">
    <svg class="emblem-area" role="img" aria-label="Large brand emblem decoration" viewBox="0 0 230 230">
      <defs>
        <linearGradient id="emblemFade" x1="1" y1="0" x2="0" y2="1">
          <stop offset="0" stop-color="#e9e2cf"/>
          <stop offset="1" stop-color="#ffffff"/>
        </linearGradient>
      </defs>
      <rect width="230" height="230" fill="url(#emblemFade)"/>
    </svg>

    <div class="brand">
      <span class="brand__mark"></span>
      <span class="brand__name">Beacon Guard Co</span>
    </div>
    <span class="brand__rule"></span>

    <div class="contact">
      <p class="contact__name">Daniel Reyes</p>
      <p class="contact__title">Managing Director</p>
      <p class="contact__address">2480 Larkspur Ave<br>Boulder, CO 80302</p>
      <ul class="contact__list">
        <li><svg viewBox="0 0 10 10"><path d="M2 0h2l1 3-1.5 1a6 6 0 0 0 2.5 2.5L7 5l3 1v2c0 1-1 2-2 2A8 8 0 0 1 0 2c0-1 1-2 2-2z"/></svg>303.555.0187</li>
        <li><svg viewBox="0 0 10 10"><path d="M0 2h10v6H0z M0 2l5 3.5L10 2" stroke="#fff" stroke-width="0.8"/></svg>hello@beaconguardco.com</li>
        <li><svg viewBox="0 0 10 10"><circle cx="5" cy="5" r="5"/></svg>www.beaconguardco.com</li>
      </ul>
    </div>
  </section>
</main>
</body>
</html>
```